Christmas Greeting Cards for Vale Works

We are looking for new Christmas greeting cards designed for our company Vale Works.
We have uploaded scans of our previous Christmas cards, each in a different format. These represent our usual style and the visual direction we would like to continue.
This year, we need updated designs featuring our new company logo.

What we are looking for:
We appreciate creative, clever and elegant designs, not generic or stock-looking graphics.
The card should feel modern, warm, and suitable for corporate clients (banks, clinics, companies, property managers but also private clients). It should be creative and sophisticated, but not too playful or cartoon-like.

Designers may also take inspiration from our cards from previous years, especially the way they used stylized graphic elements (such as water shapes or grass-like lines) to subtly reference our three sectors:

Cleaning

Gardening

Pest Control

These references must be minimal, subtle and elegant — not literal illustrations (no tools, animals, pests, etc.). Just small hints that connect the design to our identity.

Use of the Logo:
A more creative use of our new logo is highly appreciated.
We prefer layouts where the logo is integrated into the concept, not simply placed at the bottom.

Card Format:
We do not have a fixed size requirement.
You are free to choose the dimensions as long as the card is not too large (not an A4) and not too small, so that all elements remain readable and visually clear.
Vertical or horizontal formats are both welcome.

Required Sides:
The card must include both sides:

Front side: the main Christmas illustration

Back side: a space where we will insert a short thank-you message for our clients and our wishes for the new year

Text:
You may use a placeholder such as “Merry Christmas and Happy New Year” for now.
The final text will be added later. If you feel inspired, feel free to write something nice, clever, as long as it fits overall tone and style.

Tone & Purpose:
The card should:
creatively recall our logo and identity, subtly reference what we do, feel warm and corporate-friendly, express our thanks for working with us throughout the year, deliver Christmas and New Year greetings in a refined, modern way.

Target Market(s)

Building Administrators, Property Manager, Companies, Offices, Restaurants, Long-Term Business partners and Private Customers. The greeting card are intended for a professional, corporate and private clients

Industry/Entity Type

Cleaning Gardening PestControl

Requirements
Must have
• A creative and elegant use of our new logo, a clean and modern Christmas design created from scratch (not stock), subtle and stylized references to our work (cleaning–gardening–pest control), both front and back of the card, a readable format not too large or too small, and a placeholder text such as “Merry Christmas and Happy New Year” (designers may write something nice if inspired).
Nice to have
• Minimal Christmas elements (e.g., stars, snowflakes, simple winter shapes) A warm and elegant atmosphere that feels friendly but still professional Clean, modern typography, details that connects to the other cards
Should not have
• Overly decorated or busy graphics Excessive use of bright or flashy colors Generic stock images unrelated to our brand Cartoon-style illustrations or childish elements Designs that feel commercial rather than festive and elegant Distorted or altered versions of our logo, Ai feeling desing.

```html
<!DOCTYPE html>
<html lang="en">
<head>
<meta charset="utf-8">
<title>Vale Works Christmas Cards</title>
<link href="https://fonts.googleapis.com/css2?family=Montserrat:wght@500;700;800&display=swap" rel="stylesheet">
<style>
  :root {
    --gold: #e3b45a;
    --navy-bg: #12346a;
    --navy-block: #153b71;
    --navy-mark: #2d5793;
    --forest-bg: #176a1f;
    --forest-block: #1a5d21;
    --white: #ffffff;
  }
  * { margin: 0; padding: 0; box-sizing: border-box; }
  html, body { width: 900px; height: 1200px; overflow: hidden; }
  body { font-family: "Montserrat", Arial, sans-serif; }
  .sheet {
    width: 900px; height: 1200px;
    display: grid;
    grid-template-columns: 450px 450px;
    grid-template-rows: 600px 600px;
  }
  .card { position: relative; width: 450px; height: 600px; }
  .theme-navy { --bg: var(--navy-bg); --block: var(--navy-block); --mark: var(--navy-mark); }
  .theme-forest { --bg: var(--forest-bg); --block: var(--forest-block); --mark: var(--gold); }
  .card {
    background: radial-gradient(ellipse at 40% 40%, color-mix(in srgb, var(--bg) 88%, white) 0%, var(--bg) 55%, color-mix(in srgb, var(--bg) 80%, black) 100%);
  }
  .card-frame {
    position: absolute;
    left: 17px; top: 22px; width: 411px; height: 560px;
    border: 2px solid var(--gold);
  }
  .card.back .card-frame { left: 17px; }
  .greeting { position: absolute; left: 0; top: 0; width: 450px; height: 600px; }
  .greeting .block { fill: var(--block); filter: url(#soft-shadow); }
  .greeting text { fill: var(--gold); font-family: "Montserrat", Arial, sans-serif; font-weight: 700; }
  .intro {
    position: absolute; left: 39px; top: 456px; width: 190px;
    color: var(--white); font-size: 10.5px; line-height: 14.3px; font-weight: 500;
  }
  .brand {
    position: absolute; left: 39px; top: 528px;
    display: flex; align-items: center; gap: 8px;
    color: var(--mark); font-weight: 700; font-size: 19px; letter-spacing: 0.5px;
  }
  .brand-square { width: 20px; height: 20px; background: var(--mark); }
</style>
</head>
<body>
<svg width="0" height="0" style="position:absolute" aria-hidden="true">
  <defs>
    <filter id="soft-shadow" x="-10%" y="-10%" width="120%" height="120%">
      <feDropShadow dx="0" dy="1" stdDeviation="1.5" flood-color="#000" flood-opacity="0.35"/>
    </filter>
  </defs>
</svg>

<main class="sheet">
  <section class="card front theme-navy">
    <div class="card-frame"></div>
    <svg class="greeting" viewBox="0 0 450 600" role="img" aria-label="Merry Christmas and Happy New Year">
      <rect class="block" x="128" y="57" width="252" height="123"/>
      <path class="block" d="M254 180 H380 V183 A126 126 0 0 1 254 309 Z"/>
      <circle class="block" cx="191" cy="245" r="63"/>
      <path class="block" d="M185 309 H380 V423 H185 A57 57 0 0 1 185 309 Z"/>
      <path class="block" d="M257 519 V488 A61.5 61.5 0 0 1 380 488 V519 Z"/>
      <text x="143" y="111" font-size="56">ME</text>
      <text x="156" y="159" font-size="56">CH</text>
      <text x="237" y="158" font-size="120">R</text>
      <text x="311" y="122" font-size="44">RY</text>
      <text x="318" y="157" font-size="44">IS</text>
      <text x="165" y="276" font-size="88">&amp;</text>
      <text x="266" y="232" font-size="48">TM</text>
      <text x="266" y="275" font-size="48">AS</text>
      <text x="151" y="377" font-size="57" letter-spacing="2">HAPPY</text>
      <text x="276" y="408" font-size="33" letter-spacing="1.5">NEW</text>
      <text x="272" y="494" font-size="32" letter-spacing="2">YEAR</text>
    </svg>
    <p class="intro">Lorem ipsum dolor sit amet, adipiscing elit, sed do eiusmod tempor incididunt ut labore et magna aliqua.</p>
    <div class="brand"><span class="brand-square"></span><span class="brand-name">VALE WORKS</span></div>
  </section>

  <section class="card back theme-navy">
    <div class="card-frame"></div>
  </section>

  <section class="card front theme-forest">
    <div class="card-frame"></div>
    <svg class="greeting" viewBox="0 0 450 600" role="img" aria-label="Merry Christmas and Happy New Year">
      <rect class="block" x="128" y="57" width="252" height="123"/>
      <path class="block" d="M254 180 H380 V183 A126 126 0 0 1 254 309 Z"/>
      <circle class="block" cx="191" cy="245" r="63"/>
      <path class="block" d="M185 309 H380 V423 H185 A57 57 0 0 1 185 309 Z"/>
      <path class="block" d="M257 519 V488 A61.5 61.5 0 0 1 380 488 V519 Z"/>
      <text x="143" y="111" font-size="56">ME</text>
      <text x="156" y="159" font-size="56">CH</text>
      <text x="237" y="158" font-size="120">R</text>
      <text x="311" y="122" font-size="44">RY</text>
      <text x="318" y="157" font-size="44">IS</text>
      <text x="165" y="276" font-size="88">&amp;</text>
      <text x="266" y="232" font-size="48">TM</text>
      <text x="266" y="275" font-size="48">AS</text>
      <text x="151" y="377" font-size="57" letter-spacing="2">HAPPY</text>
      <text x="276" y="408" font-size="33" letter-spacing="1.5">NEW</text>
      <text x="272" y="494" font-size="32" letter-spacing="2">YEAR</text>
    </svg>
    <div class="brand"><span class="brand-square"></span><span class="brand-name">VALE WORKS</span></div>
  </section>

  <section class="card back theme-forest">
    <div class="card-frame"></div>
  </section>
</main>
</body>
</html>
```